Business Card for Multi-Brand Sportswear Company

We are looking for a business card which represents our company and the multiple brands within it.

The company: Fen Athletics (LTD)
The brands: Fen, TavaPuni, ElmStretch, Grit and Rain

Employees using these cards would be representing Fen Athletics, rather than any of the individual brands. You will see a current design within the uploaded files, to give some inspiration. The actual text of the brands is not necessary, but the logos should be on there is some format.

Our creative minds on this are stretched, so we are looking for someone to make this their own, and show us what a good business card should look like.

We may like to get these printed with spot gloss, so keep that in mind with your designs.

www.fenathletics.co.uk

Industry/Entity Type

Business

Contact Information for Business Card

Leo Pemberton-Hale
Operations Manager
(+44) 1632 960 418
Leo@fenathletics.co.uk
www.fenathletics.co.uk

Font styles to use
Sans Serif
Other font styles liked:
• Eurostile

Colors
ffffff

Requirements
Nice to have
• Dark (black) background

```html
<!DOCTYPE html>
<html lang="en">
<head>
<meta charset="utf-8">
<title>Fen Athletics – Business Card</title>
<link rel="stylesheet" href="https://fonts.googleapis.com/css2?family=Exo+2:wght@300;400;600&display=swap">
<style>
  :root {
    --stage: #3b3b3b;
    --card-white: #ffffff;
    --card-black: #000000;
    --ink: #1a1a1a;
    --ink-soft: #4a4a4a;
    --accent-red: #e3262d;
    --brand-grey: #9a9a9a;
    --brand-plum: #6b5a72;
    --white: #ffffff;
  }
  * { box-sizing: border-box; margin: 0; padding: 0; }
  html, body {
    width: 1105px; height: 1200px; overflow: hidden;
    background: var(--stage);
    font-family: "Exo 2", "Helvetica Neue", Arial, sans-serif;
  }
  .sheet { position: relative; width: 1105px; height: 1200px; }
  .card {
    position: absolute; left: 192px; width: 720px; height: 412px; overflow: hidden;
  }
  /* Front */
  .card--front { top: 146px; background: var(--card-white); }
  .front__brand {
    position: absolute; left: 42px; top: 48px;
    display: flex; align-items: center; gap: 16px;
  }
  .brand-square { width: 26px; height: 26px; background: var(--accent-red); }
  .front__brand-name {
    font-size: 46px; font-weight: 600; color: var(--ink); letter-spacing: 0.5px;
  }
  .front__band {
    position: absolute; left: 0; top: 193px; width: 100%; height: 78px;
    background: var(--card-black);
  }
  .band__accent {
    position: absolute; right: 70px; top: 0; width: 34px; height: 100%;
    background: var(--accent-red);
  }
  .person { position: absolute; left: 40px; top: 14px; }
  .person__name { font-size: 26px; font-weight: 600; color: var(--accent-red); line-height: 1.1; }
  .person__title { font-size: 19px; font-weight: 400; color: var(--white); line-height: 1.3; }
  .contact-list {
    position: absolute; left: 40px; top: 298px; list-style: none;
  }
  .contact-list li {
    display: flex; align-items: center; gap: 10px;
    font-size: 19px; font-weight: 300; color: var(--ink-soft); line-height: 28px;
  }
  .contact-list svg { width: 16px; height: 16px; fill: var(--accent-red); }
  .address {
    position: absolute; right: 38px; top: 326px; text-align: right;
    font-size: 19px; font-weight: 300; color: var(--ink-soft); line-height: 28px;
    font-style: normal;
  }
  /* Back */
  .card--back { top: 602px; background: var(--card-black); }
  .back__brand {
    position: absolute; left: 0; top: 150px; width: 100%;
    display: flex; justify-content: center; align-items: center; gap: 20px;
  }
  .back__brand .brand-square { width: 34px; height: 34px; }
  .back__brand-name { font-size: 66px; font-weight: 600; color: var(--white); }
  .brand-row {
    position: absolute; left: 0; top: 338px; width: 100%;
    display: flex; justify-content: space-around; align-items: center; padding: 0 30px;
  }
  .brand-row__item { font-size: 20px; font-weight: 600; }
  .brand-row__item--tavapuni { color: var(--brand-grey); }
  .brand-row__item--elmstretch { color: var(--brand-plum); }
  .brand-row__item--grit { color: var(--accent-red); }
  .brand-row__item--fen { color: var(--white); }
</style>
</head>
<body>
<main class="sheet">
  <section class="card card--front" aria-label="Business card front">
    <div class="front__brand">
      <span class="brand-square"></span>
      <span class="front__brand-name">Fen Athletics</span>
    </div>
    <div class="front__band">
      <div class="person">
        <p class="person__name">Tom Harrowby</p>
        <p class="person__title">Managing Director</p>
      </div>
      <span class="band__accent"></span>
    </div>
    <ul class="contact-list">
      <li>
        <svg viewBox="0 0 16 16" aria-hidden="true"><path d="M3.5 1 6 3.8 4.7 5.6c.9 2 2.6 3.7 4.7 4.7l1.8-1.3L14 11.5l-1.6 2.9C6.5 14 2 9.5 1.6 2.6z"/></svg>
        +44 (0)1632 960418
      </li>
      <li>
        <svg viewBox="0 0 16 16" aria-hidden="true"><path d="M1 3h14v1.5L8 9 1 4.5z M1 6.2 8 10.6l7-4.4V13H1z"/></svg>
        tom@fenathletics.co.uk
      </li>
      <li>
        <svg viewBox="0 0 16 16" aria-hidden="true"><path d="M8 1a7 7 0 1 0 0 14A7 7 0 0 0 8 1zm0 1.6c.9 1 1.5 2.4 1.7 4.2H6.3C6.5 5 7.1 3.6 8 2.6zM2.7 8.8h2.1c.1 1.6.5 3 1.2 4a5.4 5.4 0 0 1-3.3-4zm0-2h2.1C5 5.2 5.4 3.9 6 3a5.4 5.4 0 0 0-3.3 3.8zm5.3 6.6c-.9-1-1.5-2.5-1.7-4.6h3.4c-.2 2.1-.8 3.6-1.7 4.6zm2-.6c.7-1 1.1-2.4 1.2-4h2.1a5.4 5.4 0 0 1-3.3 4zm1.2-6c-.1-1.6-.5-2.9-1.2-3.8a5.4 5.4 0 0 1 3.3 3.8z"/></svg>
        www.fenathletics.co.uk
      </li>
    </ul>
    <address class="address">Marsh Lane, Eastby<br>Holtwick, ZZ4 9QP</address>
  </section>

  <section class="card card--back" aria-label="Business card back">
    <div class="back__brand">
      <span class="brand-square"></span>
      <span class="back__brand-name">Fen Athletics</span>
    </div>
    <div class="brand-row">
      <span class="brand-row__item brand-row__item--tavapuni">TavaPuni</span>
      <span class="brand-row__item brand-row__item--elmstretch">ElmStretch</span>
      <span class="brand-row__item brand-row__item--grit">Grit and Rain</span>
      <span class="brand-row__item brand-row__item--fen">Fen</span>
    </div>
  </section>
</main>
</body>
</html>
```